Diverse, up-scale salon needs eye-catching, unique business cards.

We are looking for a unique business card design for our stylist but that can also be multi functional and used for appointment reminder and referrals. I will need a design in a format that I can modify names and titles going forward. In the past we have had a dark background with the logo on one side, and stylist and contact information on the other but we are open to all ideas. I have included our mission statement as well as branded colors below. The statement doesn't need to go on the card, it's just a reference for target market. We need space for the stylists name, title, instagram handle and then the salons phone number, website and address. I am also open to adding a spot for a qr code linked to the stylist instagram or the salon booking link.

primary brand colors:
#333333 #233415 #36502a #93874a #000000
Mission statement:
Vessolin Hair Studio, a high-end salon located in the lively Downtown Farmington, Michigan, is committed to providing exceptional services in a welcoming and relaxed environment to meet the needs of our diverse clientele.
Our salon specializes in contemporary custom haircuts, coloring, extensions, and barbering and beard grooming services. Our team of skilled stylists is passionate and inventive in their hair styling techniques. At the heart of our salon are values centered on quality, innovation, creativity, and above all, comfort. These core values are evident in every appointment across our customizable array of services.
Our goal is to establish a benchmark for exceptional hair care for every human.
Website: www.vessolinhairstudio.example
instagram: @vessolinhairstudio
address: 41782 Pelham Crest Rd, Brookvale OR
phone: 555-613-4087

Industry/Entity Type

Hair Salon

Contact Information for Business Card

Stylist name, title, phone, instagram, website, address, (optional qr code)

Requirements
Should not have
• Does not need mission statement on the card.

```html
<!DOCTYPE html>
<html lang="en">
<head>
<meta charset="utf-8">
<title>Vessolin Hair Studio — Business Card</title>
<link href="https://fonts.googleapis.com/css2?family=Arimo:wght@400;700&display=swap" rel="stylesheet">
<style>
  :root {
    --backdrop: #1c1c1c;
    --gold: #93874a;
    --grey: #777777;
    --text-grey: #7a7a7a;
    --white: #ffffff;
  }
  * { margin: 0; padding: 0; box-sizing: border-box; }
  html, body {
    width: 1200px; height: 1059px; overflow: hidden;
    background: var(--backdrop);
    font-family: "Arimo", Arial, sans-serif;
  }
  .card {
    position: absolute;
    overflow: hidden;
    box-shadow: 0 10px 30px rgba(0,0,0,0.6);
  }
  .card-front { left: 258px; top: 89px; width: 689px; height: 394px; background: var(--white); }
  .card-back  { left: 252px; top: 541px; width: 701px; height: 400px; background: var(--gold); }

  .brand-mark {
    position: absolute;
    display: flex; flex-direction: column; align-items: center; gap: 14px;
    text-align: center;
  }
  .brand-ring { border-radius: 50%; border-style: solid; }
  .brand-name { font-weight: 700; letter-spacing: 2px; line-height: 1.25; }

  .card-front .brand-mark { left: 116px; top: 86px; width: 200px; }
  .card-front .brand-ring { width: 96px; height: 96px; border-width: 3px; border-color: var(--gold); }
  .card-front .brand-name { color: var(--gold); font-size: 17px; }

  .divider { position: absolute; left: 344px; top: 71px; width: 2px; height: 193px; background: var(--text-grey); }

  .contact { position: absolute; left: 373px; top: 67px; color: var(--text-grey); }
  .person-name { color: var(--gold); font-weight: 700; font-size: 20px; line-height: 20px; }
  .person-title { font-size: 17.5px; line-height: 18px; }
  .address { margin-top: 20px; font-size: 18px; line-height: 24px; }
  .contact-list { list-style: none; margin-top: 10px; }
  .contact-list li { display: flex; align-items: center; gap: 10px; font-size: 18.5px; line-height: 28px; }
  .contact-list svg { width: 15px; height: 15px; flex: none; margin-top: 4px; }

  .wave { position: absolute; left: 0; top: 0; width: 689px; height: 394px; }

  .card-back .brand-mark { left: 225px; top: 74px; width: 250px; }
  .card-back .brand-ring { width: 140px; height: 140px; border-width: 4px; border-color: var(--white); }
  .card-back .brand-name { color: var(--white); font-size: 22px; }

  .services-heading {
    position: absolute; left: 48px; top: 319px; width: 604px; height: 26px;
    display: flex; align-items: center; gap: 6px;
  }
  .services-heading .rule { flex: 1; height: 1.5px; background: var(--white); }
  .services-heading .pill {
    background: var(--white); color: var(--gold); font-weight: 700; font-size: 19px;
    padding: 2px 9px; border-radius: 14px; line-height: 21px;
  }
  .services-list {
    position: absolute; left: 47px; top: 351px; width: 607px;
    list-style: none; display: flex; justify-content: space-between;
    color: var(--white); font-size: 17.5px; white-space: nowrap;
  }
  .services-list li::before {
    content: ""; display: inline-block; width: 7px; height: 7px; border-radius: 50%;
    background: var(--white); margin-right: 4px; vertical-align: 2px;
  }
</style>
</head>
<body>

<section class="card card-front">
  <div class="brand-mark">
    <div class="brand-ring"></div>
    <div class="brand-name">VESSOLIN<br>HAIR STUDIO</div>
  </div>

  <div class="divider"></div>

  <div class="contact">
    <div class="person-name">MARCUS DELANEY</div>
    <div class="person-title">Manager</div>
    <div class="address">41782 Pelham Crest Rd<br>Brookvale OR</div>
    <ul class="contact-list">
      <li>
        <svg viewBox="0 0 16 16" aria-hidden="true"><path d="M3 1.5l2.5 0 1.2 3.2-1.6 1.2c.8 1.8 2.2 3.2 4 4l1.2-1.6 3.2 1.2 0 2.5c0 .8-.7 1.5-1.5 1.5C6.6 13.5 2.5 9.4 1.5 4.6 1.5 2.8 2.2 1.5 3 1.5z" fill="var(--gold)"/></svg>
        555-613-4087
      </li>
      <li>
        <svg viewBox="0 0 16 16" aria-hidden="true"><rect x="2" y="2" width="12" height="12" rx="2" fill="none" stroke="var(--gold)" stroke-width="2"/></svg>
        @vessolinhairstudio
      </li>
      <li>
        <svg viewBox="0 0 16 16" aria-hidden="true"><g fill="none" stroke="var(--gold)" stroke-width="1.4"><circle cx="8" cy="8" r="6.5"/><ellipse cx="8" cy="8" rx="3" ry="6.5"/><path d="M1.5 8h13M2.5 4.8h11M2.5 11.2h11"/></g></svg>
        www.vessolinhairstudio.example
      </li>
    </ul>
  </div>

  <svg class="wave" viewBox="0 0 689 394" aria-hidden="true">
    <path d="M0,296 C40,330 110,348 220,346 C320,344 400,322 465,305 C400,322 320,352 230,363 C130,374 40,365 0,332 Z" fill="var(--grey)"/>
    <path d="M0,334 C60,378 150,384 250,372 C380,356 500,296 620,290 C650,289 672,292 689,297 L689,394 L0,394 Z" fill="var(--gold)"/>
  </svg>
</section>

<section class="card card-back">
  <div class="brand-mark">
    <div class="brand-ring"></div>
    <div class="brand-name">VESSOLIN<br>HAIR STUDIO</div>
  </div>

  <div class="services-heading">
    <span class="rule"></span>
    <span class="pill">OUR SERVICES</span>
    <span class="rule"></span>
  </div>
  <ul class="services-list">
    <li>Custom Haircuts</li>
    <li>Coloring</li>
    <li>Extensions</li>
    <li>And Barbering</li>
    <li>Beard Grooming</li>
  </ul>
</section>

</body>
</html>
```